Counseling Practice Business Card

I need a professional looking business card incorporating my new logo that was just completed. Card needs to incorporate my name and title, description of my specialty, my address, my phone number, my fax number, my email and my website URL. I need to be able to choose design on/with different paper colors and textures.
I do not have a lot of business card ideas so I am open to anything but I want bold,sharp, clear card without additional designs other than my logo (see attached file info). I am open to different color backgrounds or paper colors including black. I do not like traditional brackets around area codes in phone number or dashes between numbers in phone number. Am open to other ways of presenting including periods between numbers as appropriate. I do not know enough to know what I like yet but I want card to coordinate and work together with my logo. My practice emphasizes natural mental health interventions so any use of color (with background paper color or the blue and green in my logo) that elicits nature is nice. In addition to black, any natural brown or wood looking background might be desirable also. Most of the offerings so far look very similar and boring.

Target Market(s)

Potential therapy clients and other professionals

Contact Information for Business Card

Card information:
Gerald M. Whitcombe, Ph.D.
Licensed Clinical Psychologist
Integrative Health Coach
4812 Marlowe Ridge Blvd SE
Suite 310
Duluth, GA 30096
(770) 415-2983 phone
(770) 581-4096 fax
drgeraldwhitcombe@quillmarsh.net
brightfernwellness.net

Font styles to use
Serif
Sans Serif
Other font styles liked:
• anything that you think looks crisp, clear and easily readable

Requirements
Must have
• Any color used should coordinate with my logo design (see attached files).
• Card should be printed horizontally so top and bottom are longest sides of rectangle.
• Background color or paper color should complement and highlight logo. Do not like a white background. black, grey, brown or any color my logo would blend well with.
Nice to have
• I would like designer to utilize color to highlight letters/name or phone-fax-web symbols.
• Bottom edge of card could be highlighted if appropriate to an idea.
Should not have
• I would NOT want the card to have a pure white background at all.
• No clear cards.
• Cards should be oriented with long sides on bottom and top, NOT sides. DO NOT LIKE THIS THIN TALL ORIENTATION.

```html
<!DOCTYPE html>
<html lang="en">
<head>
<meta charset="utf-8">
<title>Brightfern Wellness – Business Card</title>
<link rel="stylesheet" href="https://fonts.googleapis.com/css2?family=Oswald:wght@400;500&display=swap">
<style>
  :root {
    --backdrop: #b8bcbc;
    --kraft: #d8b39b;
    --kraft-edge: #c9a389;
    --ink-brown: #9a6a44;
    --rule-brown: #a97a55;
    --brand-green: #1f7a3a;
    --brand-blue: #2f86d0;
  }
  * { margin: 0; padding: 0; box-sizing: border-box; }
  html, body {
    width: 1200px;
    height: 824px;
    overflow: hidden;
    background: var(--backdrop);
    font-family: "Oswald", "Arial Narrow", sans-serif;
  }
  .stage {
    width: 1200px;
    height: 824px;
    display: flex;
    align-items: center;
    justify-content: center;
    gap: 48px;
  }
  .card {
    width: 540px;
    height: 309px;
    background: var(--kraft);
    border: 1px solid var(--kraft-edge);
    position: relative;
  }
  /* Back: contact details */
  .card--back {
    padding: 0 0 34px 44px;
    display: flex;
    flex-direction: column;
    justify-content: flex-end;
    color: var(--ink-brown);
  }
  .contact-name {
    font-size: 19px;
    font-weight: 500;
    letter-spacing: 0.2px;
    line-height: 1.2;
  }
  .contact-title {
    font-size: 13.5px;
    font-weight: 400;
    line-height: 1.35;
  }
  .divider {
    width: 36px;
    height: 1px;
    background: var(--rule-brown);
    margin: 11px 0 10px;
  }
  .contact-line {
    font-size: 13px;
    font-weight: 400;
    line-height: 1.4;
  }
  /* Front: practice name */
  .card--front {
    display: flex;
    align-items: center;
    justify-content: center;
    gap: 14px;
  }
  .brand-dot {
    width: 22px;
    height: 22px;
    border-radius: 50%;
    background: var(--brand-blue);
  }
  .brand-name {
    font-size: 40px;
    font-weight: 500;
    color: var(--brand-green);
    letter-spacing: 0.5px;
  }
</style>
</head>
<body>
  <main class="stage">
    <section class="card card--back" aria-label="Business card back with contact details">
      <p class="contact-name">Gerald M. Whitcombe, Ph.D.</p>
      <p class="contact-title">Licensed Clinical Psychologist</p>
      <p class="contact-title">Integrative Health Coach</p>
      <div class="divider"></div>
      <p class="contact-line">(770) 415-2983 phone</p>
      <p class="contact-line">(770) 581-4096 fax</p>
      <p class="contact-line">drgeraldwhitcombe@quillmarsh.net</p>
      <p class="contact-line">brightfernwellness.net</p>
      <div class="divider"></div>
      <p class="contact-line">4812 Marlowe Ridge Blvd SE</p>
      <p class="contact-line">Suite 310, Duluth, GA 30096</p>
    </section>
    <section class="card card--front" aria-label="Business card front with practice name">
      <span class="brand-dot"></span>
      <h1 class="brand-name">Brightfern Wellness</h1>
    </section>
  </main>
</body>
</html>
```